Business Card Design

Buy and sell properties
Buy and rehab properties
Buy properties for cash
That is what I do but do need a logo
looking for some type of logo or design on it
Just started business
Back of card should say something like BUY HOUSES CASH
Overview: it is a new company. Basically I buy properties wholesale and fix them up and sell them or sell them to other fix and flippers
Background: company is new so not any background
Market: is basically anyone selling a house or buying a house. Someone that needs to sell house fast. Basically I am a cash home buyer!!!

Updates
Email on card should be:   harborlanerealtyinc@mailnest.com

Industry/Entity Type
House
Contact Information for Business Card
Harbor Lane Realty Inc
PO Box 718296
Coral Mill Key FL 33071

Dwight Kallum
dkallum@mailnest.com
305-271-5589

```html
<!DOCTYPE html>
<html lang="en">
<head>
<meta charset="utf-8">
<title>Harbor Lane Realty Inc – Business Card</title>
<link href="https://fonts.googleapis.com/css2?family=Tinos:wght@400;700&display=swap" rel="stylesheet">
<style>
  :root {
    --bg: #d9d4cc;
    --card: #ffffff;
    --ink: #111111;
    --brand-red: #861b1b;
    --on-red: #f3e9e9;
  }
  * { margin: 0; padding: 0; box-sizing: border-box; }
  html, body { width: 1200px; height: 858px; overflow: hidden; }
  body {
    background: var(--bg);
    font-family: "Tinos", "Times New Roman", serif;
    color: var(--ink);
    display: flex;
    align-items: center;
    justify-content: center;
    gap: 40px;
  }
  .card {
    position: relative;
    width: 540px;
    height: 308px;
    background: var(--card);
    box-shadow: 0 6px 18px rgba(0,0,0,0.18);
    overflow: hidden;
  }
  .brand-name {
    font-family: "Tinos", "Times New Roman", serif;
    font-weight: 700;
    font-size: 30px;
    line-height: 1.05;
    color: var(--ink);
  }
  /* Front */
  .card-front .brand-name {
    position: absolute;
    left: 34px;
    top: 92px;
  }
  .holder-name {
    position: absolute;
    right: 46px;
    top: 88px;
    font-size: 24px;
  }
  .divider {
    position: absolute;
    left: 0;
    top: 168px;
    width: 540px;
    height: 14px;
  }
  .contact {
    position: absolute;
    top: 198px;
    font-size: 13px;
    white-space: nowrap;
  }
  .contact-phone { left: 50px; }
  .contact-email { left: 160px; }
  .contact-address { left: 318px; }
  /* Back */
  .card-back .brand-name {
    position: absolute;
    left: 0;
    right: 0;
    top: 62px;
    text-align: center;
  }
  .tagline-band {
    position: absolute;
    left: 0;
    bottom: 0;
    width: 100%;
    height: 112px;
    background: var(--brand-red);
    display: flex;
    align-items: center;
    padding-left: 64px;
  }
  .tagline {
    color: var(--on-red);
    font-size: 22px;
    letter-spacing: 1px;
  }
</style>
</head>
<body>

  <section class="card card-front" aria-label="Card front">
    <div class="brand-name">Harbor Lane<br>Realty Inc</div>
    <div class="holder-name">Dwight Kallum</div>

    <svg class="divider" viewBox="0 0 540 14" aria-hidden="true">
      <g fill="var(--ink)">
        <rect x="0" y="5" width="44" height="5"/>
        <rect x="64" y="5" width="90" height="5"/>
        <rect x="174" y="5" width="132" height="5"/>
        <rect x="328" y="5" width="212" height="5"/>
        <!-- phone -->
        <path d="M50 2 q-3 0 -3 4 q1 5 6 7 q3 0 4 -2 l-2 -2 l-2 1 q-2 -1 -3 -3 l1 -2 z"/>
        <!-- envelope -->
        <rect x="156" y="2" width="16" height="10"/>
        <path d="M156 2 l8 6 l8 -6" stroke="#fff" stroke-width="1.2" fill="none"/>
        <!-- pin -->
        <path d="M317 1 a5 5 0 0 1 5 5 q0 3 -5 8 q-5 -5 -5 -8 a5 5 0 0 1 5 -5 z"/>
        <circle cx="317" cy="6" r="1.8" fill="#fff"/>
      </g>
    </svg>

    <div class="contact contact-phone">305-271-5589</div>
    <div class="contact contact-email">dkallum@mailnest.com</div>
    <div class="contact contact-address">718296 Coral Mill Key FL 33071</div>
  </section>

  <section class="card card-back" aria-label="Card back">
    <div class="brand-name">Harbor Lane<br>Realty Inc</div>
    <div class="tagline-band">
      <span class="tagline">BUY HOUSES CASH</span>
    </div>
  </section>

</body>
</html>
```